ADA COMPLIANCE

We are in need of flyer or tri fold page for ada compliance, handicap ramps and parking lot striping.

Target Market(s)

Commercial Construction Industry

Industry/Entity Type

Parking

Font styles to use
Other font styles liked:
• Felix Titling

Colors
0355a3
acd036

Requirements
Must have
• Our Company Name and logo, 8005172934 number License #2847306
• List of services provided in uploaded images. Navy blue with high vizability green

```html
<!DOCTYPE html>
<html lang="en">
<head>
<meta charset="utf-8">
<title>Vanguard Build Services – ADA Tri-fold</title>
<link href="https://fonts.googleapis.com/css2?family=Cinzel:wght@600&family=Lato:wght@400;700;900&family=Oswald:wght@400;600&display=swap" rel="stylesheet">
<style>
  :root {
    --navy: #0355a3;
    --navy-deep: #1d3b72;
    --green: #acd036;
    --paper: #ffffff;
    --ink: #1a2238;
    --stage: #e7e8ea;
  }
  * { box-sizing: border-box; margin: 0; padding: 0; }
  html, body { width: 1200px; height: 898px; overflow: hidden; }
  body { background: var(--stage); font-family: "Lato", sans-serif; color: var(--ink); }

  .trifold {
    position: absolute; left: 30px; top: 29px;
    width: 1140px; height: 840px;
    display: flex;
    box-shadow: 0 10px 30px rgba(0,0,0,.18);
  }
  .panel { position: relative; width: 380px; height: 840px; background: var(--paper); overflow: hidden; }
  .panel svg.shapes { position: absolute; inset: 0; }

  .photo { position: absolute; }
  .photo--lot { background: linear-gradient(170deg, #c9d6e0 0%, #8f8a86 30%, #4f4743 70%, #3c3532 100%); }
  .photo--tents { background: linear-gradient(160deg, #bcd3ea 0%, #d9c46a 35%, #3b5ea8 55%, #3a3a3e 100%); }

  .brand { position: absolute; text-align: center; }
  .brand__name { font-family: "Cinzel", serif; font-weight: 600; color: var(--navy-deep); letter-spacing: 1px; line-height: 1; }
  .brand__sub { font-family: "Lato", sans-serif; font-size: 8px; letter-spacing: 1.5px; color: var(--navy-deep); margin-top: 3px; }
  .brand__mark { display: inline-block; width: 12px; height: 12px; border-radius: 50%; background: var(--navy-deep); margin-bottom: 6px; }

  /* left panel */
  .services__ribbon {
    position: absolute; left: 0; top: 180px; width: 380px; height: 36px;
    background: var(--navy-deep); color: #fff; font-size: 14px; font-weight: 700;
    display: flex; align-items: center; padding-left: 18px;
  }
  .services__list { position: absolute; top: 236px; list-style: none; font-size: 14.5px; line-height: 21px; color: var(--ink); }
  .services__list li::before { content: "•"; color: var(--navy); margin-right: 6px; }
  .services__list--a { left: 22px; }
  .services__list--b { left: 200px; }

  /* middle panel */
  .contact { position: absolute; left: 0; top: 520px; width: 380px; text-align: center; color: #fff; }
  .contact__call { font-weight: 900; font-size: 26px; color: var(--green); }
  .contact__phone { font-weight: 900; font-size: 34px; margin-top: 6px; }
  .contact__mail { font-weight: 700; font-size: 18px; margin-top: 8px; }
  .contact__web { font-weight: 700; font-size: 17px; letter-spacing: 7px; margin-top: 12px; }
  .access-badge { position: absolute; left: 115px; top: 352px; width: 150px; height: 150px; }

  /* right panel */
  .tagline { position: absolute; left: 0; top: 590px; width: 380px; text-align: center; color: var(--navy-deep); font-family: "Oswald", sans-serif; }
  .tagline__lead { font-weight: 400; font-size: 32px; }
  .tagline__strong { font-weight: 600; font-size: 26px; }
  .tagline__web { font-family: "Lato", sans-serif; font-weight: 700; font-size: 17px; letter-spacing: 7px; margin-top: 12px; color: var(--navy); }
</style>
</head>
<body>
<main class="trifold">

  <section class="panel panel--services">
    <svg class="shapes" width="380" height="840" viewBox="0 0 380 840">
      <path d="M0 0H380V18C260 28 120 48 0 78Z" fill="var(--navy-deep)"/>
      <path d="M0 78C120 48 260 28 380 18V30C260 40 120 60 0 90Z" fill="var(--green)"/>
      <path d="M0 520H380V560C250 540 120 540 0 575Z" fill="var(--navy-deep)"/>
      <path d="M0 575C120 540 250 540 380 560V572C250 552 120 552 0 587Z" fill="var(--green)"/>
      <path d="M0 790C130 770 260 760 380 740V840H0Z" fill="var(--green)"/>
    </svg>
    <div class="brand" style="left:0;top:100px;width:380px">
      <span class="brand__mark"></span>
      <div class="brand__name" style="font-size:28px">VANGUARD</div>
      <div class="brand__sub">BUILD SERVICES INC</div>
    </div>
    <div class="services__ribbon">There is nothing we cannot do, but we specialize in:</div>
    <ul class="services__list services__list--a">
      <li>New Construction,</li><li>Tenant Improvement,</li><li>Building Alterations,</li>
      <li>Design/Build,</li><li>Retail,</li><li>Hotel,</li><li>Casinos,</li>
      <li>Fueling Stations</li><li>Shopping Malls,</li><li>Auto Facilities,</li>
      <li>Financial Institutions,</li><li>Parking Structures,</li>
    </ul>
    <ul class="services__list services__list--b">
      <li>Electrical,</li><li>Plumbing,</li><li>Flooring,</li><li>ADA Improvements</li>
      <li>/Modifications,</li><li>Drywall,</li><li>Painting,</li><li>Restaurants,</li>
      <li>Custom Concrete,</li><li>Foundations,</li><li>Framing,</li><li>Roofing...And MORE</li>
    </ul>
    <div class="photo photo--tents" role="img" aria-label="Freshly striped parking lot with accessible spaces beside large event tents and a delivery truck" style="left:0;top:587px;width:380px;height:203px;clip-path:polygon(0 0,100% 0,100% 75%,0 100%)"></div>
  </section>

  <section class="panel panel--contact">
    <svg class="shapes" width="380" height="840" viewBox="0 0 380 840">
      <path d="M0 0H380V20C260 30 130 50 0 80Z" fill="var(--green)"/>
      <path d="M0 440C130 420 260 410 380 400V760C260 770 130 780 0 800Z" fill="var(--navy-deep)"/>
      <path d="M0 430C130 410 260 400 380 390V400C260 410 130 420 0 440Z" fill="var(--green)"/>
      <path d="M0 800C130 780 260 770 380 760V840H0Z" fill="var(--green)"/>
    </svg>
    <div class="photo photo--lot" role="img" aria-label="Worker striping a parking lot with a line-marking machine, city skyline behind" style="left:0;top:0;width:380px;height:430px;clip-path:polygon(0 19%,100% 5%,100% 90.7%,0 100%)"></div>
    <svg class="access-badge" viewBox="0 0 150 150" aria-label="Accessibility symbol">
      <polygon points="75,4 138,40 138,110 75,146 12,110 12,40" fill="var(--green)"/>
      <polygon points="75,16 127,46 127,104 75,134 23,104 23,46" fill="#fff"/>
      <g fill="none" stroke="var(--navy-deep)" stroke-width="7" stroke-linecap="round" stroke-linejoin="round">
        <circle cx="66" cy="40" r="6" fill="var(--navy-deep)" stroke="none"/>
        <path d="M64 54V80H90L100 104"/>
        <path d="M64 66H84"/>
        <path d="M54 66A24 24 0 1 0 88 98"/>
      </g>
    </svg>
    <div class="contact">
      <div class="contact__call">CALL US NOW:</div>
      <div class="contact__phone">+1 800 517 2934</div>
      <div class="contact__mail">E-mail: info@vanguardbs.com</div>
      <div class="contact__web">www.vanguardbs.com</div>
    </div>
  </section>

  <section class="panel panel--cover">
    <div class="photo photo--lot" role="img" aria-label="Worker with a striping machine laying blue and white lines across a parking lot" style="left:0;top:0;width:380px;height:500px"></div>
    <svg class="shapes" width="380" height="840" viewBox="0 0 380 840">
      <path d="M0 0H380V150H0Z" fill="#fff" opacity=".92"/>
      <path d="M0 0H140C90 10 40 30 0 50Z" fill="var(--green)"/>
      <path d="M0 430C130 470 260 440 380 390V840H0Z" fill="var(--green)"/>
      <path d="M0 445C130 485 260 455 380 405V770C260 790 130 800 0 810Z" fill="#fff"/>
    </svg>
    <div class="brand" style="left:0;top:40px;width:380px">
      <span class="brand__mark"></span>
      <div class="brand__name" style="font-size:36px">VANGUARD</div>
      <div class="brand__sub" style="font-size:10px">BUILD SERVICES INC</div>
    </div>
    <div class="tagline">
      <div class="tagline__lead">We set new standards for</div>
      <div class="tagline__strong">Design, Quality and Craftsmanship</div>
      <div class="tagline__web">www.vanguardbs.com</div>
    </div>
  </section>

</main>
</body>
</html>
```